Construction company business card

One side to be the logo with the company name, The other side I would like: (Tomas verbick) Project manager 41 barrow crescent hallam 52917306224783(03) 9703 2428Info@gudeljgroup.comAnd then maybe a couple dot points saying what we do:Construction (commercial & industrial) Civil construction

Anything else please contact me!
Maybe curved st one edge of the card

Target Market(s)

Older clientele

Industry/Entity Type

Construction Company

Contact Information for Business Card

Read above

Colors
3277b5
1b1b1b
9d9d9d

Requirements
Must have
• Use my logo on one side
Nice to have
• Read above
Should not have
• Read above

```html
<!DOCTYPE html>
<html lang="en">
<head>
<meta charset="utf-8">
<title>Stonefield – Business Card</title>
<link href="https://fonts.googleapis.com/css2?family=Roboto:wght@400;500;700&display=swap" rel="stylesheet">
<style>
  :root {
    --brand-blue: #3277b5;
    --brand-dark: #1b1b1b;
    --brand-grey: #9d9d9d;
    --card-face: #f1f1f1;
    --backdrop: #b9b9b9;
    --text-body: #3a3a3a;
  }
  * { box-sizing: border-box; margin: 0; padding: 0; }
  html, body {
    width: 1200px; height: 576px; overflow: hidden;
    background: var(--backdrop);
    font-family: "Roboto", Arial, sans-serif;
  }
  .stage { position: relative; width: 1200px; height: 576px; }

  .card {
    position: absolute;
    top: 138px;
    width: 484px;
    height: 294px;
    background: var(--card-face);
    border-top-right-radius: 34px;
    overflow: hidden;
  }
  .card--front { left: 82px; border-bottom-left-radius: 14px; }
  .card--back  { left: 602px; }

  /* shared brand block */
  .mark-dot { border-radius: 50%; background: var(--brand-blue); }
  .brand-name {
    font-weight: 700; letter-spacing: 1px; line-height: 1;
    color: var(--brand-blue); text-transform: uppercase;
  }

  /* front */
  .front-mark {
    position: absolute; left: 0; right: 0; top: 36px;
    display: flex; flex-direction: column; align-items: center;
  }
  .front-mark .mark-dot { width: 112px; height: 112px; }
  .front-mark .brand-name { margin-top: 14px; font-size: 38px; }

  .front-web {
    position: absolute; left: 0; right: 0; top: 235px;
    display: flex; justify-content: center; align-items: center; gap: 10px;
    font-size: 12.5px; color: var(--text-body);
  }
  .front-web .rule { width: 34px; height: 2px; background: var(--brand-grey); }
  .front-services {
    position: absolute; left: 0; right: 0; top: 256px;
    text-align: center; font-size: 13px; color: var(--text-body);
  }
  .front-band {
    position: absolute; left: 0; right: 0; bottom: 0; height: 10px;
    display: flex;
  }
  .front-band .band-grey { flex: 0 0 50%; background: var(--brand-grey); }
  .front-band .band-blue { flex: 1; background: var(--brand-blue); }

  /* back */
  .contact {
    position: absolute; right: 258px; top: 60px; text-align: right;
  }
  .contact-name { font-weight: 700; font-size: 16px; color: var(--brand-blue); }
  .contact-role { font-size: 12px; color: var(--text-body); margin-top: 5px; }
  .contact-lines { list-style: none; margin-top: 22px; }
  .contact-lines li {
    font-size: 12px; color: var(--text-body); height: 19px;
    display: flex; justify-content: flex-end; align-items: center; gap: 10px;
  }
  .contact-lines svg { width: 10px; height: 10px; fill: var(--brand-grey); }
  .contact-address { font-size: 12px; color: var(--text-body); margin-top: 6px; margin-right: 20px; }

  .back-mark {
    position: absolute; left: 272px; width: 180px; top: 60px;
    display: flex; flex-direction: column; align-items: center;
  }
  .back-mark .mark-dot { width: 86px; height: 86px; }
  .back-mark .brand-name { font-size: 28px; margin-top: 12px; }

  .back-base {
    position: absolute; left: 0; right: 0; bottom: 0; height: 22px;
    background: var(--brand-grey);
  }
  .back-tab {
    position: absolute; left: 28px; bottom: 0; width: 428px; height: 38px;
  }
  .back-tab svg { position: absolute; inset: 0; }
  .back-tab span {
    position: relative; display: block; text-align: center;
    line-height: 38px; font-size: 12px; color: #fff;
  }
</style>
</head>
<body>
<main class="stage">

  <section class="card card--front" aria-label="Card front">
    <div class="front-mark">
      <div class="mark-dot"></div>
      <div class="brand-name">Stonefield</div>
    </div>
    <p class="front-web"><span class="rule"></span>www.stonefieldproperty.com<span class="rule"></span></p>
    <p class="front-services">Construction (Commercial &amp; Industrial) Civil Construction</p>
    <div class="front-band"><span class="band-grey"></span><span class="band-blue"></span></div>
  </section>

  <section class="card card--back" aria-label="Card back">
    <div class="contact">
      <h1 class="contact-name">Daniel Harwood</h1>
      <p class="contact-role">Project Manager</p>
      <ul class="contact-lines">
        <li>(04) 2736 5190
          <svg viewBox="0 0 10 10"><path d="M1 4 Q5 0 9 4 L8 5 L6.5 4 L6.5 3 Q5 2.5 3.5 3 L3.5 4 L2 5 Z M2.5 5.5 H7.5 L8.5 9 H1.5 Z"/></svg></li>
        <li>(03) 8125 4067
          <svg viewBox="0 0 10 10"><path d="M0.5 2 H9.5 V8 H0.5 Z M1 2.6 L5 5.6 L9 2.6 V3.3 L5 6.3 L1 3.3 Z" fill-rule="evenodd"/></svg></li>
        <li>info@stonefieldgroup.com
          <svg viewBox="0 0 10 10"><circle cx="5" cy="5" r="4.3" fill="none" stroke="#9d9d9d" stroke-width="0.9"/><ellipse cx="5" cy="5" rx="1.8" ry="4.3" fill="none" stroke="#9d9d9d" stroke-width="0.8"/><path d="M0.7 5 H9.3" stroke="#9d9d9d" stroke-width="0.8"/></svg></li>
      </ul>
      <p class="contact-address">17 Kestrel Lane Mooreland 3950</p>
    </div>

    <div class="back-mark">
      <div class="mark-dot"></div>
      <div class="brand-name">Stonefield</div>
    </div>

    <div class="back-base"></div>
    <div class="back-tab">
      <svg viewBox="0 0 428 38" preserveAspectRatio="none" aria-hidden="true">
        <path d="M0 38 L14 6 Q17 0 24 0 H404 Q411 0 414 6 L428 38 Z" fill="#3277b5"/>
      </svg>
      <span>Construction (Commercial &amp; Industrial) Civil Construction</span>
    </div>
  </section>

</main>
</body>
</html>
```